Hollow Meridian Book website design.

This is a simple one-page web design for my book.
I have all files and video needed.
Domain listed with Net Harbor.
Password and username will be given to winning bid.
Domain address, www.hollowmeridian.info
Upload a 30 second video so it can be played on the website.
Book cover photo
Book Blurb text.
Links to Rivermart and Audio books where the book can be purchased.
Below is the link to the Rivermart listing.
https://www.rivermart.example/dp/X00AAAAAA1/?coliid=QWERTYUIOPASD&colid=1ZXCVBNMLKJH0&psc=0&ref_=lv_ov_lig_dp_i
Below is the link to my Listenly books.com listing.
https://www.listenly.example/pd/Hollow-Meridian-Audiobook/X00BBBBBB2?qid=1000000001&sr=1-7&ref=a_search_c3_lProduct_1_7&pf_rd_p=00000000-aaaa-bbbb-cccc-000000000000&pf_rd_r=ZZZZ00000000000000QQ
Text on page.” Click on either logo to go directly to Rivermart or Listenly.com
Link Listenly book logo to my book on Listenly.com
Place this text under Listenly.com logo: “Free to new members of Listenly.com”
Link Rivermart logo to my book on Rivermart.
Place this text under Rivermart logo “ Free to new Pagewisp members on Rivermart.com”
Link the book photo to the Rivermart.com web address as well.
Enter meta tags or keywords below for search engines to locate webpage.
Hollow Meridian
Conspiracy
Conspiracy Books
Spy books
Thriller books
Suspense books
Comedy books
Dorian Welbeck

```html
<!DOCTYPE html>
<html lang="en">
<head>
<meta charset="utf-8">
<title>Hollow Meridian</title>
<meta name="keywords" content="Hollow Meridian, Conspiracy, Conspiracy Books, Spy books, Thriller books, Suspense books, Comedy books, Dorian Welbeck">
<link href="https://fonts.googleapis.com/css2?family=Nunito:wght@400;600;700;800&family=PT+Sans:wght@700&display=swap" rel="stylesheet">
<style>
:root{
  --navy:#2d2f6b;
  --ring:#8d8eb3;
  --red:#a8102c;
  --ink:#2a2a35;
  --footer:#0f0f17;
  --white:#ffffff;
}
*{margin:0;padding:0;box-sizing:border-box}
html,body{width:1200px;height:2649px;overflow:hidden;background:var(--white);font-family:'Nunito',sans-serif;color:var(--ink)}
a{color:inherit;text-decoration:none}
section,footer{position:relative;width:1200px}
.hero{height:600px;background:linear-gradient(180deg,#8a8279 0%,#a49a79 22%,#6f6650 45%,#3e3c33 75%,#2f2e2a 100%)}
.hero .site-name{position:absolute;left:112px;top:27px;color:var(--white);font-weight:700;font-size:17px;letter-spacing:.2px}
.hero .menu{position:absolute;left:1064px;top:28px;width:24px;height:18px}
.hero .menu span{display:block;height:3px;background:var(--white);margin-bottom:4.5px;border-radius:2px}
.hero-copy{position:absolute;left:0;top:240px;width:1200px;text-align:center;color:var(--white)}
.hero-copy h1{font-family:'PT Sans',sans-serif;font-size:39px;font-weight:700;letter-spacing:.3px;margin-bottom:16px;color:#f3f1ee}
.hero-copy p{width:720px;margin:0 auto;font-size:15.5px;line-height:26px}
.btn{display:inline-block;margin-top:13px;width:130px;height:39px;line-height:39px;border-radius:20px;background:var(--red);color:var(--white);font-size:15px;font-weight:600}
.book{height:613px}
.book.second{height:602px}
.cover-circle{position:absolute;width:412px;height:412px;border-radius:50%;background:var(--ring)}
.cover-circle::after{content:"";position:absolute;inset:11px;border-radius:50%;background:var(--navy)}
.cover-art{position:absolute;width:300px;height:440px;border-radius:4px;background:linear-gradient(160deg,#1f2a6b 0%,#7a1020 35%,#202020 60%,#0a0a0a 100%)}
.book.first .cover-circle{left:115px;top:84px}
.book.first .cover-art{left:178px;top:82px;transform:rotate(-12deg)}
.book.second .cover-circle{left:675px;top:84px}
.book.second .cover-art{left:735px;top:72px;transform:rotate(8deg);background:linear-gradient(170deg,#050505 0%,#111 45%,#3a3a3a 70%,#0b0b0b 100%)}
.blurb{position:absolute;width:490px}
.book.first .blurb{left:600px;top:92px}
.book.second .blurb{left:112px;top:95px}
.blurb h2{font-size:31px;font-weight:800;color:var(--navy);letter-spacing:.3px;line-height:40px}
.blurb .rule{width:139px;height:3px;background:var(--red);margin:6px 0 20px}
.blurb p{font-size:14px;line-height:25.7px;text-align:justify}
.store{display:flex;align-items:center;margin-top:14px;font-size:16.5px;font-weight:700;color:var(--navy)}
.store .badge{margin-left:10px;padding:0 8px;height:37px;line-height:37px;font-size:15px;font-weight:700}
.badge.dark{background:#111;color:var(--white)}
.badge.light{background:var(--white);color:var(--ink);box-shadow:0 1px 5px rgba(0,0,0,.2);height:50px;line-height:50px;padding:0 10px}
.go{display:block;margin-top:16px;font-size:16.5px;font-weight:700;color:var(--navy)}
.video{height:537px;background:radial-gradient(circle at 62% 45%,#b9a08f 0%,#4a4ca0 25%,#2e3290 60%,#23276f 100%)}
.play{position:absolute;left:567px;top:1481px;width:66px;height:66px}
.footer{height:297px;background:var(--footer);color:var(--white);text-align:center}
.footer h3{padding-top:56px;font-size:21px;font-weight:700;letter-spacing:.4px}
.contacts{display:flex;justify-content:center;gap:46px;margin-top:18px;font-size:15.5px}
.contacts span{display:flex;align-items:center;gap:9px}
.social{display:flex;justify-content:center;gap:13px;margin-top:28px}
.social a{width:42px;height:42px;border-radius:50%;background:var(--navy);font-size:12px;font-weight:700;line-height:42px}
.copyright{margin-top:24px;font-size:14.5px;font-weight:600;letter-spacing:.8px}
</style>
</head>
<body>
<section class="hero" role="img" aria-label="Aerial photograph of a capital city skyline at sunset">
  <div class="site-name">HOLLOW MERIDIAN</div>
  <div class="menu"><span></span><span></span><span></span></div>
  <div class="hero-copy">
    <h1>WELCOME TO HOLLOW MERIDIAN</h1>
    <p>Lorem ipsum dolor sit amet, consectetur adipiscing elit, sed do eiusmod tempor incididunt ut labore et dolore magna aliqua. Ut enim ad minim veniam, quis nostrud exercitation ullamco laboris nisi ut aliquip ex ea commodo consequat.</p>
    <a class="btn" href="#">Learn More</a>
  </div>
</section>

<section class="book first">
  <div class="cover-circle"></div>
  <a class="cover-art" href="https://www.rivermart.example/dp/X00AAAAAA1/?coliid=QWERTYUIOPASD&colid=1ZXCVBNMLKJH0&psc=0&ref_=lv_ov_lig_dp_i" role="img" aria-label="Hardcover book Hollow Meridian by Dorian Welbeck, flag and portrait cover"></a>
  <div class="blurb">
    <h2>HOLLOW MERIDIAN</h2>
    <div class="rule"></div>
    <p>A fictional novel based on current events surrounding the covid 19 virous. Jack Holman is a well-respected independent journalist contracted by the Eastbridge Chronicle, upon his return from reporting on the war in Syria he is tasked to investigate the covid virus outbreak in China. As he digs deeper, he uncovers a hideous plot by the powers that be here in America. Jack risks life and limb to uncover the conspirers behind all of this and shed light to the American people.</p>
    <div class="store">Free To New Pagewisp Members On :<a class="badge dark" href="https://www.rivermart.example/dp/X00AAAAAA1/?coliid=QWERTYUIOPASD&colid=1ZXCVBNMLKJH0&psc=0&ref_=lv_ov_lig_dp_i">Rivermart</a></div>
    <a class="go" href="https://www.rivermart.example/dp/X00AAAAAA1/?coliid=QWERTYUIOPASD&colid=1ZXCVBNMLKJH0&psc=0&ref_=lv_ov_lig_dp_i">Click to go directly to Rivermart.com</a>
  </div>
</section>

<section class="video" role="img" aria-label="Video still of a man in a suit raising his arms before a starry blue backdrop"></section>
<svg class="play" viewBox="0 0 66 66" aria-hidden="true">
  <circle cx="33" cy="33" r="33" fill="#a8102c" opacity=".35"/>
  <circle cx="33" cy="33" r="24" fill="#a8102c"/>
  <path d="M28 25 L41 33 L28 41 Z" fill="#fff"/>
</svg>

<section class="book second">
  <div class="blurb">
    <h2>HOLLOW MERIDIAN</h2>
    <div class="rule"></div>
    <p>A fictional novel based on current events surrounding the covid 19 virous. Jack Holman is a well-respected independent journalist contracted by the Eastbridge Chronicle, upon his return from reporting on the war in Syria he is tasked to investigate the covid virus outbreak in China. As he digs deeper, he uncovers a hideous plot by the powers that be here in America. Jack risks life and limb to uncover the conspirers behind all of this and shed light to the American people.</p>
    <div class="store">Free to new members of :<a class="badge light" href="https://www.listenly.example/pd/Hollow-Meridian-Audiobook/X00BBBBBB2?qid=1000000001&sr=1-7&ref=a_search_c3_lProduct_1_7&pf_rd_p=00000000-aaaa-bbbb-cccc-000000000000&pf_rd_r=ZZZZ00000000000000QQ">Listenly</a></div>
    <a class="go" href="https://www.listenly.example/pd/Hollow-Meridian-Audiobook/X00BBBBBB2?qid=1000000001&sr=1-7&ref=a_search_c3_lProduct_1_7&pf_rd_p=00000000-aaaa-bbbb-cccc-000000000000&pf_rd_r=ZZZZ00000000000000QQ">Click&nbsp; to go directly to&nbsp; Listenly.com</a>
  </div>
  <div class="cover-circle"></div>
  <div class="cover-art" role="img" aria-label="Black hardcover book with script title and a profile portrait"></div>
</section>

<footer class="footer">
  <h3>HOLLOW MERIDIAN</h3>
  <div class="contacts">
    <span><svg width="16" height="16" viewBox="0 0 16 16"><path d="M15 1 L1 7 L7 9 L9 15 Z" fill="#fff"/></svg>2003 Lorem ipsum dolor sit 0612</span>
    <span><svg width="16" height="16" viewBox="0 0 16 16"><path d="M3 1 L6 1 L7 5 L5 6.5 Q7 9.5 9.5 11 L11 9 L15 10 L15 13 Q14 15 12 15 Q2 13 1 4 Q1 2 3 1 Z" fill="#fff"/></svg>Phone: +1 888 888 8888</span>
    <span><svg width="16" height="13" viewBox="0 0 16 13"><rect x="0" y="0" width="16" height="13" rx="1.5" fill="#fff"/><path d="M1 1.5 L8 7 L15 1.5" stroke="#0f0f17" stroke-width="1.6" fill="none"/></svg>Email: info@hollowmeridian.info</span>
  </div>
  <div class="social">
    <a href="#" aria-label="Postwall">Ps</a>
    <a href="#" aria-label="Chirpwave">Cw</a>
    <a href="#" aria-label="Pixkeep">Pk</a>
    <a href="#" aria-label="Worknet">Wn</a>
    <a href="#" aria-label="Glimmer">Gl</a>
  </div>
  <div class="copyright">Copyright © 2022. All Rights Reserved.</div>
</footer>
</body>
</html>
```